New Pump Website Design Needed

We need a homepage concept for a pump website rebuild.

The navigation at the top must be:
Home - About Us - Pump Stations - Pumps - Electrical - Drainage - Environmental - Accessories - Contact Us

The homepage should have the the following structure:
Logo
Navigation
Rotating Banner
Content + Picture of PDF Flipbook to download/ view
Featured Products (in one row - approx 4)
Footer

The footer must include:
Left side - navigation small.
"Copyright KelvoRun 2014. All Rights reserved"

Right side: "Website by Pixel Orchard Studio"

Content and imagery, and Logo can be taken from their existing website: tarnbrookvalves.co.nz

We have attached a copy of their New PDF - the new website design must reflect this (Use block colours/ different colours for the navigation items/ incorporate the footer image).

Industry/Entity Type

Electrical

Font styles to use
Sans Serif

Requirements
Must have
• Features from their brochure brought in (colour scheme and footer feature)
Should not have
• Any Social Media Icons

```html
<!DOCTYPE html>
<html lang="en">
<head>
<meta charset="utf-8">
<title>KelvoRun Pump Systems</title>
<link href="https://fonts.googleapis.com/css2?family=Open+Sans:wght@400;600;700&display=swap" rel="stylesheet">
<style>
:root{
  --sky-top:#7fb1d8;
  --sky-mid:#d6e8f4;
  --sky-low:#5d9ccd;
  --brand-blue:#0b4f9c;
  --nav-top:#2283d2;
  --nav-bottom:#0a5aa8;
  --panel-blue:#0a4e98;
  --panel-button:#163d73;
  --text:#555;
  --dark:#222;
  --btn-red:#c4101b;
  --white:#fff;
}
*{box-sizing:border-box;margin:0;padding:0}
html,body{width:1067px;height:1200px;overflow:hidden}
body{
  font-family:"Open Sans",Arial,sans-serif;
  background:linear-gradient(180deg,var(--sky-top) 0%,var(--sky-mid) 50%,var(--sky-low) 100%);
  position:relative;color:var(--text);
}
.page{position:absolute;left:90px;top:28px;width:889px;height:1154px;background:var(--white)}
.abs{position:absolute}

/* header */
.brand{left:17px;top:22px;height:60px;display:flex;align-items:center;gap:8px}
.brand-mark{width:18px;height:18px;background:var(--brand-blue)}
.brand-name{font-weight:700;font-size:28px;color:var(--brand-blue);letter-spacing:.5px}
.contact-icon{top:36px}
.contact-text{top:38px;font-size:11.5px;line-height:16px;color:#666;white-space:nowrap}
.divider-v{top:22px;width:1px;height:48px;background:#e2e2e2}
.btn-contact{left:778px;top:34px;width:92px;height:27px;background:#000;color:var(--white);font-size:11px;display:flex;align-items:center;justify-content:center}

/* navigation */
.main-nav{left:17px;top:97px;width:853px;height:36px;display:flex;background:linear-gradient(180deg,var(--nav-top),var(--nav-bottom))}
.main-nav a{color:var(--white);text-decoration:none;font-size:13px;display:flex;align-items:center;justify-content:center;border-right:1px solid rgba(255,255,255,.25)}
.main-nav a:last-child{border-right:none}
.main-nav .active{background:linear-gradient(180deg,#d21a24,#9e0d15)}

/* banner */
.banner{left:17px;top:148px;width:587px;height:381px;background:linear-gradient(180deg,#8b6e5e 0%,#a7a29c 40%,#9fb6c4 65%,#c2ccd2 100%)}
.slide-arrow{top:190px;width:22px;height:22px;border-radius:50%;background:rgba(255,255,255,.55);display:flex;align-items:center;justify-content:center}
.slide-caption{right:34px;top:210px;width:260px;text-align:center;color:#111}
.slide-caption h2{font-weight:400;font-size:27px;line-height:34px}
.slide-caption p{font-size:15px;line-height:19px;margin-top:4px}
.dots{left:344px;top:540px;display:flex;gap:7px}
.dots span{width:6px;height:6px;border-radius:50%;background:#bbb}
.dots .on{background:var(--brand-blue)}

/* quick contact */
.quick{left:622px;top:148px;width:248px;height:381px;background:var(--panel-blue)}
.quick h3{font-weight:400;color:var(--white);font-size:22px;text-align:center;padding-top:16px;height:56px;border-bottom:1px solid rgba(255,255,255,.15)}
.field{position:absolute;left:34px;width:182px;background:var(--white);border:1px solid #c9d4e2;font-size:11px;color:#444;padding:6px 12px}
.field.select{display:flex;justify-content:space-between;padding-right:0;align-items:center;padding-top:0;padding-bottom:0}
.field.select i{width:24px;height:26px;background:var(--panel-button);color:var(--white);font-style:normal;font-size:9px;display:flex;align-items:center;justify-content:center}
.btn-send{position:absolute;left:34px;top:305px;width:182px;height:28px;background:var(--panel-button);color:var(--white);font-size:11px;display:flex;align-items:center;justify-content:center}

/* content */
.section-title{font-weight:400;color:var(--brand-blue);font-size:17px;line-height:22px;text-transform:uppercase}
.welcome-title{left:17px;top:578px}
.guide-title{left:538px;top:578px}
.team-photo{left:18px;top:619px;width:111px;height:133px;background:linear-gradient(180deg,#eef2f6,#b9c8d6)}
.welcome-text{left:151px;top:615px;width:354px;font-size:11.6px;line-height:17px;text-align:justify}
.btn{position:absolute;height:24px;color:var(--white);font-size:12.5px;display:flex;align-items:center;justify-content:center}
.btn.dark{background:linear-gradient(180deg,#4a4a4a,#222)}
.btn.red{background:var(--btn-red)}
.cover{left:540px;top:619px;width:92px;height:133px;background:linear-gradient(180deg,#1a6bb8 0%,#3d9ad6 50%,#0f4e91 80%,#d9a23a 82%,#1a5ea8 100%)}
.guide-head{left:646px;top:615px;font-size:15px;color:var(--dark)}
.guide-text{left:646px;top:636px;width:224px;font-size:11.6px;line-height:16px;text-align:justify}

/* featured */
.featured-head{left:0;top:804px;width:889px;height:26px;display:flex;justify-content:center;align-items:center;gap:20px}
.featured-head .section-title{font-size:18px;line-height:26px}
.round{width:16px;height:16px;border-radius:50%;display:flex;align-items:center;justify-content:center}
.product{position:absolute;top:850px;width:199px}
.product .frame{height:136px;border:3px solid #e6e6e6;display:flex;align-items:center;justify-content:center;background:var(--white)}
.product .shot{width:110px;height:108px}
.product .name{text-align:center;font-size:15px;color:#333;margin-top:8px}
.product .name.link{color:var(--brand-blue)}

/* footer */
.footer{left:0;top:1065px;width:889px;height:89px;background:linear-gradient(180deg,#2b86cf,#0a4f9a)}
.footer-nav{position:absolute;top:15px;width:100%;text-align:center;font-size:11.6px;color:var(--white)}
.footer-nav span{margin:0 6px}
.footer-rule{position:absolute;top:45px;left:0;width:100%;height:1px;background:rgba(255,255,255,.25)}
.footer-copy{position:absolute;top:60px;left:19px;font-size:11.6px;color:var(--white)}
.footer-credit{position:absolute;top:60px;right:21px;font-size:11.6px;color:var(--white)}
</style>
</head>
<body>
<div class="page">
  <header>
    <div class="abs brand"><span class="brand-mark"></span><span class="brand-name">KelvoRun</span></div>
    <svg class="abs contact-icon" style="left:428px" width="16" height="20" viewBox="0 0 16 20"><path d="M4 1 L7 5 L5 8 Q7 12 10 14 L12 12 L15 16 L12 19 Q3 15 1 4 Z" fill="var(--brand-blue)"/></svg>
    <div class="abs divider-v" style="left:447px"></div>
    <span class="abs contact-text" style="left:455px">0800-555-019</span>
    <svg class="abs contact-icon" style="left:567px;top:39px" width="22" height="15" viewBox="0 0 22 15"><rect x="1" y="1" width="20" height="13" fill="none" stroke="var(--brand-blue)" stroke-width="1.6"/><path d="M1 1 L11 9 L21 1 M1 14 L8 7 M21 14 L14 7" fill="none" stroke="var(--brand-blue)" stroke-width="1.4"/></svg>
    <div class="abs divider-v" style="left:596px"></div>
    <span class="abs contact-text" style="left:603px;font-size:11px">sales@tarnbrookvalves.co.nz</span>
    <div class="abs btn-contact">Contact US</div>
  </header>

  <nav class="abs main-nav">
    <a class="active" style="width:90px">Home</a>
    <a style="width:140px">Pump Stations</a>
    <a style="width:94px">Pumps</a>
    <a style="width:106px">Electrical</a>
    <a style="width:105px">Drainage</a>
    <a style="width:142px">Environmental</a>
    <a style="width:176px">Accessories</a>
  </nav>

  <section class="abs banner" role="img" aria-label="Two blue submersible pumps with float switches standing in floodwater in front of a brick building">
    <div class="abs slide-arrow" style="left:19px"><svg width="8" height="12"><path d="M6 1 L2 6 L6 11" fill="none" stroke="#fff" stroke-width="2"/></svg></div>
    <div class="abs slide-arrow" style="left:550px"><svg width="8" height="12"><path d="M2 1 L6 6 L2 11" fill="none" stroke="#fff" stroke-width="2"/></svg></div>
    <div class="abs slide-caption">
      <h2>Nam quis magna</h2>
      <p>Sapien.Nullam magna lacus,<br>molestinon augue et.</p>
    </div>
  </section>
  <div class="abs dots"><span class="on"></span><span></span><span></span></div>

  <aside class="abs quick">
    <h3>QUICK CONTACT</h3>
    <div class="field" style="top:84px;height:27px">Name</div>
    <div class="field" style="top:120px;height:27px">Email</div>
    <div class="field" style="top:155px;height:27px">Phone</div>
    <div class="field" style="top:189px;height:48px">Address</div>
    <div class="field select" style="top:244px;height:27px"><span>Service For</span><i>▼</i></div>
    <div class="btn-send">CONTACT NOW</div>
  </aside>

  <h2 class="abs section-title welcome-title">Welcome to Tarnbrook Valves</h2>
  <div class="abs team-photo" role="img" aria-label="Smiling team of three staff members"></div>
  <p class="abs welcome-text">To achieve our mission statement we have a large range of pumps &amp; equipment. From domestic, commercial &amp; civil pumping stations to industrial pumps, reticulation systems, to farm pumps ... we look after every pumping need, large or small.Many desktop publishing packages and web page editors now use Lorem Ipsum as their default model text.</p>
  <div class="btn dark" style="left:417px;top:730px;width:87px">Read More</div>

  <h2 class="abs section-title guide-title">Download our Product Guide</h2>
  <div class="abs cover" role="img" aria-label="Cover of the general product catalogue with a water ripple photo"></div>
  <div class="abs guide-head">Flip Book</div>
  <p class="abs guide-text">dolor sit amet, consectetur adipiscing elit. Donec tristique malesuada erat quis posuere. Maecenas sed lacinia massa. Morbi quis dolor eu arcu commodo commodo.</p>
  <div class="btn dark" style="left:694px;top:730px;width:59px">View</div>
  <div class="btn red" style="left:762px;top:730px;width:107px">Download Here</div>

  <div class="abs featured-head">
    <span class="round" style="background:var(--brand-blue)"><svg width="8" height="10"><path d="M6 1 L2 5 L6 9" fill="none" stroke="#fff" stroke-width="2"/></svg></span>
    <h2 class="section-title">Featured Products</h2>
    <span class="round" style="background:#aaa"><svg width="8" height="10"><path d="M2 1 L6 5 L2 9" fill="none" stroke="#fff" stroke-width="2"/></svg></span>
  </div>

  <div class="product" style="left:18px">
    <div class="frame"><div class="shot" role="img" aria-label="Blue gate valve with handwheel" style="background:radial-gradient(circle,#2f6fc4 30%,#fff 70%)"></div></div>
    <div class="name link">Lorem Ipsum Dolor</div>
  </div>
  <div class="product" style="left:236px">
    <div class="frame"><div class="shot" role="img" aria-label="Coiled flexible hoses in blue, orange and grey" style="background:radial-gradient(circle,#e49a2a 20%,#3b4fa0 45%,#fff 72%)"></div></div>
    <div class="name">Contantry Popilar</div>
  </div>
  <div class="product" style="left:454px">
    <div class="frame"><div class="shot" role="img" aria-label="Stainless steel submersible drainage pump" style="background:radial-gradient(circle,#8d969e 25%,#2b333b 45%,#fff 72%)"></div></div>
    <div class="name">Ipsum Dolor</div>
  </div>
  <div class="product" style="left:672px">
    <div class="frame"><div class="shot" role="img" aria-label="Black submersible pump with yellow float switch" style="background:radial-gradient(circle,#1d1d1d 35%,#d7c13a 48%,#fff 72%)"></div></div>
    <div class="name">Lorem Ipsum Dolor</div>
  </div>

  <footer class="abs footer">
    <div class="footer-nav">Home<span>|</span>About Us<span>|</span>Pump Stations<span>|</span>Pumps<span>|</span>Electrical<span>|</span>Drainage<span>|</span>Environmental<span>|</span>Accessories<span>|</span>Contact Us</div>
    <div class="footer-rule"></div>
    <div class="footer-copy">Copyright KelvoRun 2014. All Rights reserved</div>
    <div class="footer-credit">Website by Pixel Orchard Studio</div>
  </footer>
</div>
</body>
</html>
```